Webdesign für Kleingruppenreisen in die Südsteiermark
Zielgruppe
Wir sind ein Start-Up Unternehmen, das als Kleingruppenreisen in die Südsteiermark veranstaltet; der Schwerpunkt liegt auf dem Kulinarischen. Zielgruppe sind Geschäftsleute, die diese Kurzreisen (Do-So) für Marketingzwecke oder als Mitarbeiterbonus (oder auch privat) nutzen möchten.
Aufgabenstellung
Die Homepage soll eine Online-Shop Möglichkeit bieten, in der die Reise (bisher gibt es nur einen Ablauf) gebucht werden kann. Optisch sollte sie sich an das bereits von Ihnen erstellte Logo anlehnen und möglichst ansprechende Fotos von der Südsteiermark, Graz, Leoben usw. enthalten. (Siehe die beiden Flyer und das Logo)
Wir haben inzwischen Bildfreigaben von Haldauer und dem Tourismusverband Kellwinden erhalten und können auch eigene Bilder zur Verfügung stellen. Bitte kontaktieren Sie uns dafür, wenn nötig.

```html
<!DOCTYPE html>
<html lang="de">
<head>
<meta charset="utf-8">
<title>Feinreise Kellwinden – Kleingruppenreisen Südsteiermark</title>
<link href="https://fonts.googleapis.com/css2?family=Lato:wght@300;400;700;900&family=Kaushan+Script&display=swap" rel="stylesheet">
<style>
:root{
  --orange:#f15a24;
  --yellow:#f7d51d;
  --red:#e8432a;
  --green:#3fbf48;
  --footer-green:#5ec639;
  --ink:#222;
  --grey-text:#444;
  --panel:#f4f4f4;
  --black:#000;
  --bar:#1b1b1b;
  --white:#fff;
}
*{margin:0;padding:0;box-sizing:border-box}
html,body{width:1200px;height:3307px;overflow:hidden}
body{position:relative;font-family:'Lato',sans-serif;color:var(--ink);background:#fff}
.abs{position:absolute}
/* header */
.site-header{left:0;top:0;width:1200px;height:90px;background:#fff}
.brand{left:88px;top:28px;width:184px;height:92px;background:#fff;display:flex;align-items:center;gap:8px;padding-left:10px;z-index:3}
.brand-mark{flex:none;width:14px;height:14px;background:var(--red);border-radius:50%}
.brand-name{font-weight:900;font-size:15px;color:var(--red);line-height:1.1;white-space:nowrap}
.main-nav{right:88px;top:27px;display:flex;font-size:15.5px}
.main-nav a{display:block;padding:11px 15px;color:var(--ink);text-decoration:none;height:42px}
.main-nav a.active{background:var(--yellow);border-radius:3px;padding:11px 20px}
/* hero */
.hero{left:0;top:90px;width:1200px;height:475px;background:linear-gradient(180deg,#e0683a,#d9742f 60%,#c7652a)}
.hero-script{left:0;top:140px;width:1200px;text-align:center;font-family:'Kaushan Script',cursive;font-size:96px;color:#fff;line-height:1}
.hero-title{left:0;width:1200px;text-align:center;font-weight:300;color:#fff;font-size:72px;line-height:1;letter-spacing:1px}
.hero-sub{left:0;top:456px;width:1200px;text-align:center;font-weight:900;font-size:25px;color:#2a1208}
.hero-dots{left:590px;top:525px;display:flex;gap:7px}
.hero-dots span{width:14px;height:14px;border-radius:50%;background:#fff}
.hero-dots span:first-child{background:var(--yellow)}
/* why */
.why-brand{left:540px;top:592px;width:200px;height:66px;display:flex;align-items:center;justify-content:center;gap:6px}
.why-title{left:0;top:683px;width:1200px;text-align:center;font-size:36px;font-weight:400;color:var(--ink)}
.why-title b{color:var(--yellow);font-weight:700}
.why-text{left:170px;top:745px;width:860px;text-align:center;font-size:20px;font-weight:300;line-height:35px;color:var(--grey-text)}
.gallery-item{top:870px;width:221px;height:208px;box-shadow:0 8px 10px rgba(0,0,0,.3)}
.arrow-btn{width:48px;height:48px;border-radius:50%;background:var(--orange);display:flex;align-items:center;justify-content:center}
/* inspired */
.inspired{left:0;top:1118px;width:1200px;height:427px}
.inspired-title{left:0;top:1150px;width:1200px;text-align:center;font-family:'Kaushan Script',cursive;font-size:58px;color:#fff}
.video{left:306px;top:1242px;width:584px;height:290px;background:linear-gradient(180deg,#b9ae93,#b5a386)}
.video-bar{left:306px;top:1532px;width:584px;height:36px;background:#222}
/* features */
.feature{top:1610px;width:240px}
.feature-icon{width:50px;height:50px;background:var(--green);border-radius:3px;display:flex;align-items:center;justify-content:center}
.feature-name{position:absolute;left:66px;top:3px;font-size:15px;line-height:19px;color:#555}
.feature-text{margin-top:30px;font-size:12px;line-height:27px;font-weight:300;color:#444;width:210px;text-align:justify}
/* packages */
.packages-title{left:0;top:1842px;width:1200px;text-align:center;font-size:32px;font-weight:400;color:var(--ink)}
.packages-title b{color:var(--yellow);font-weight:700}
.packages-rule{left:548px;top:1893px;width:104px;height:4px;background:#333}
.package{left:88px;top:1925px;width:1024px;height:430px;background:var(--panel);overflow:hidden}
.package-title{left:0;top:30px;width:1000px;text-align:center;font-size:36px;font-weight:900;color:var(--red);letter-spacing:-.5px}
.package-photo{left:28px;top:93px;width:415px;height:312px;background:linear-gradient(180deg,#7fb0d6 0%,#6f9a4a 35%,#5c7e34 60%,#a98b6a 100%)}
.small-arrow{width:26px;height:26px;border-radius:50%;background:var(--orange);display:flex;align-items:center;justify-content:center}
.offer-heading{left:470px;top:147px;width:480px;text-align:right;font-size:25px;font-weight:400;color:var(--red);line-height:31px}
.offer-rule{left:862px;top:222px;width:88px;height:3px;background:var(--orange)}
.offer-text{left:486px;top:250px;width:489px;text-align:justify;text-align-last:right;font-size:16.5px;line-height:24.5px;color:#333}
.ribbon{left:892px;top:0;width:132px;height:132px;overflow:hidden}
.ribbon span{position:absolute;left:-15px;top:35px;width:190px;height:34px;background:var(--green);color:#fff;font-weight:900;font-size:15px;text-align:center;line-height:34px;transform:rotate(45deg);white-space:nowrap}
/* why best */
.why-best{left:0;top:2372px;width:1200px;height:543px;background:var(--orange)}
.tabs{left:88px;top:2427px;width:492px;height:68px;background:#f0f0f0;display:flex;font-size:20px;font-weight:700}
.tab{height:68px;display:flex;align-items:center;padding:0 18px;color:#333;white-space:nowrap}
.tab.active{background:#fff;border-bottom:4px solid var(--green);padding:0 33px}
.tab-text{left:88px;top:2532px;width:490px;font-size:17px;line-height:31px;color:var(--yellow);text-align:justify}
.devices{left:610px;top:2390px;width:590px;height:510px;background:linear-gradient(160deg,#f2f2f2 0%,#c9c9c9 45%,#ef8a52 100%);opacity:.85;clip-path:polygon(45% 0,100% 5%,100% 70%,55% 100%,0 55%)}
/* footer */
.footer-line{left:0;top:2912px;width:1200px;height:10px;background:var(--yellow)}
.site-footer{left:0;top:2922px;width:1200px;height:338px;background:var(--black)}
.footer-h{top:2943px;font-size:19px;font-weight:700;color:var(--footer-green)}
.footer-links{font-size:13.5px;line-height:35.5px;list-style:none;color:var(--white)}
.footer-links .strong{font-size:15px;font-weight:700}
.contact-row{left:442px;display:flex;gap:18px;font-size:12px;line-height:26px;color:var(--white)}
.contact-row svg{flex:none;margin-top:2px}
.field{left:834px;width:278px;background:#fff;color:#777;font-size:15px;padding:8px 20px}
.submit{left:834px;top:3180px;width:141px;height:41px;background:var(--yellow);color:#111;font-size:18px;text-align:center;line-height:41px}
.footer-brand{left:252px;top:3142px;width:144px;height:78px;background:#fff;display:flex;align-items:center;justify-content:center;gap:6px}
.copyright{left:0;top:3260px;width:1200px;height:47px;background:var(--bar);color:#fff;text-align:center;font-size:12px;line-height:44px}
</style>
</head>
<body>

<header class="abs site-header">
  <nav class="abs main-nav">
    <a class="active" href="#">HOME</a><a href="#">SERVICES</a><a href="#">ONLINE SHOP</a><a href="#">BLOG</a><a href="#">LEGAL</a><a href="#">CONTACT</a>
  </nav>
</header>

<section class="abs hero" role="img" aria-label="Foto einer belebten Altstadtgasse in Graz mit orangefarbener Tönung"></section>
<div class="abs brand"><span class="brand-mark"></span><span class="brand-name">Feinreise Kellwinden</span></div>
<div class="abs hero-script">Explore</div>
<div class="abs hero-title" style="top:255px">DREAM</div>
<div class="abs hero-title" style="top:355px">DESTINATION</div>
<div class="abs hero-sub">YOUR DREAM COMES TRUE HERE</div>
<div class="abs hero-dots"><span></span><span></span><span></span><span></span></div>

<div class="abs why-brand"><span class="brand-mark"></span><span class="brand-name">Feinreise Kellwinden</span></div>
<h2 class="abs why-title">Why Choosing <b>US?</b></h2>
<p class="abs why-text">Lorem Ipsum is simply dummy text of the printing and typesetting industry. Lorem Ipsum has been the industry's standard dummy text ever since the 1500s</p>

<div class="abs gallery-item" style="left:133px;background:linear-gradient(180deg,#3e8fd4,#5d8a5c 55%,#b9b0a4)" role="img" aria-label="Foto eines Sees mit Bergdorf"></div>
<div class="abs gallery-item" style="left:370px;background:linear-gradient(180deg,#2f6fcf,#7aa6e0 55%,#b8ae9c)" role="img" aria-label="Foto einer Mariensäule in der Stadt"></div>
<div class="abs gallery-item" style="left:607px;background:linear-gradient(180deg,#c7dbe8,#6c9a38 35%,#4d7a22)" role="img" aria-label="Foto der südsteirischen Weinberge"></div>
<div class="abs gallery-item" style="left:843px;background:linear-gradient(180deg,#7fa964,#c8453a 50%,#8a8a8a)" role="img" aria-label="Foto einer roten Standseilbahn"></div>
<div class="abs arrow-btn" style="left:113px;top:949px"><svg width="16" height="16" viewBox="0 0 16 16"><path d="M10 3 5 8l5 5" stroke="#fff" stroke-width="2.5" fill="none"/></svg></div>
<div class="abs arrow-btn" style="left:1035px;top:949px"><svg width="16" height="16" viewBox="0 0 16 16"><path d="m6 3 5 5-5 5" stroke="#fff" stroke-width="2.5" fill="none"/></svg></div>

<svg class="abs inspired" width="1200" height="427" viewBox="0 0 1200 427" role="img" aria-label="Foto einer hügeligen Weinlandschaft mit orangefarbener Tönung">
  <defs><linearGradient id="insp" x1="0" y1="0" x2="0" y2="1"><stop offset="0" stop-color="#f08b3c"/><stop offset=".55" stop-color="#d9782f"/><stop offset="1" stop-color="#a85a22"/></linearGradient></defs>
  <path d="M0 0Q600 50 1200 0V427H0Z" fill="url(#insp)"/>
</svg>
<div class="abs inspired-title">Get Inspired</div>
<div class="abs video" role="img" aria-label="Videovorschau: Radfahrer auf einem Weg durch die Weinberge"></div>
<svg class="abs" style="left:511px;top:1306px" width="162" height="162" viewBox="0 0 162 162"><circle cx="81" cy="81" r="74" fill="#fff" stroke="#000" stroke-width="12"/><path d="M61 48v66l55-33Z" fill="#000"/></svg>
<div class="abs video-bar">
  <svg width="584" height="36" viewBox="0 0 584 36">
    <circle cx="26" cy="18" r="11" fill="#555"/><path d="M23 12v12l9-6Z" fill="#ddd"/>
    <rect x="48" y="15" width="270" height="6" rx="3" fill="#111"/><circle cx="53" cy="18" r="5" fill="#fff"/>
    <rect x="330" y="8" width="80" height="20" rx="10" fill="#111"/>
    <text x="345" y="22" font-family="Lato,sans-serif" font-size="11" fill="#fff">00:00 / <tspan fill="#e33">00:00</tspan></text>
    <path d="M450 14h4l5-4v16l-5-4h-4Z" fill="#bbb"/>
    <rect x="470" y="15" width="50" height="6" rx="3" fill="#111"/><circle cx="499" cy="18" r="5" fill="#fff"/>
    <rect x="530" y="10" width="38" height="16" rx="3" fill="#444"/>
  </svg>
</div>

<div class="abs feature" style="left:88px">
  <div class="feature-icon"><svg width="30" height="30" viewBox="0 0 30 30" fill="none" stroke="#fff" stroke-width="1.6"><path d="M5 13a10 10 0 0 1 20 0Z"/><path d="M10 13l3 8M20 13l-3 8"/><rect x="12" y="21" width="6" height="6"/></svg></div>
  <div class="feature-name">Special<br>Activities</div>
  <p class="feature-text">Lorem Ipsum is simply dummy text of the printing and typesetting industry. Lorem Ipsum has been the industry's standard dummy text ever since the 1500s</p>
</div>
<div class="abs feature" style="left:355px">
  <div class="feature-icon"><svg width="32" height="30" viewBox="0 0 32 30" fill="none" stroke="#fff" stroke-width="1.6"><path d="M3 17l24-4c3 0 3 3 0 4L10 21l-5-2Z"/><path d="M12 15 9 7h3l6 7"/><path d="M4 25h24"/></svg></div>
  <div class="feature-name">Travel<br>Arrangements</div>
  <p class="feature-text">Lorem Ipsum is simply dummy text of the printing and typesetting industry. Lorem Ipsum has been the industry's standard dummy text ever since the 1500s</p>
</div>
<div class="abs feature" style="left:632px">
  <div class="feature-icon"><svg width="30" height="30" viewBox="0 0 30 30" fill="none" stroke="#fff" stroke-width="1.6"><circle cx="15" cy="15" r="12"/><path d="m19 11-2 6-6 2 2-6Z"/></svg></div>
  <div class="feature-name">Private<br>Guide</div>
  <p class="feature-text">Lorem Ipsum is simply dummy text of the printing and typesetting industry. Lorem Ipsum has been the industry's standard dummy text ever since the 1500s</p>
</div>
<div class="abs feature" style="left:905px">
  <div class="feature-icon"><svg width="30" height="30" viewBox="0 0 30 30" fill="none" stroke="#fff" stroke-width="1.6"><path d="M15 27s-8-9-8-15a8 8 0 0 1 16 0c0 6-8 15-8 15Z"/><circle cx="15" cy="12" r="3"/></svg></div>
  <div class="feature-name">Location<br>Manager</div>
  <p class="feature-text">Lorem Ipsum is simply dummy text of the printing and typesetting industry. Lorem Ipsum has been the industry's standard dummy text ever since the 1500s</p>
</div>

<h2 class="abs packages-title">BEST HOLIDAY <b>PACKAGES</b></h2>
<div class="abs packages-rule"></div>

<article class="abs package">
  <h3 class="abs package-title">THE GREEN HEART OF AUSTRIA - VACATIONS STYRIA</h3>
  <div class="abs package-photo" role="img" aria-label="Foto von Weingläsern und Trauben auf einem Tisch vor Weinbergen"></div>
  <div class="abs small-arrow" style="left:911px;top:98px"><svg width="10" height="10" viewBox="0 0 10 10"><path d="M6.5 1.5 3 5l3.5 3.5" stroke="#fff" stroke-width="2" fill="none"/></svg></div>
  <div class="abs small-arrow" style="left:950px;top:98px"><svg width="10" height="10" viewBox="0 0 10 10"><path d="M3.5 1.5 7 5 3.5 8.5" stroke="#fff" stroke-width="2" fill="none"/></svg></div>
  <h4 class="abs offer-heading">WINTER STAY FOR SINGLE COUPLE @<br>$250.00 FOR 2 NIGHTS</h4>
  <div class="abs offer-rule"></div>
  <p class="abs offer-text">Lorem Ipsum is simply dummy text of the printing and typesetting industry. Lorem Ipsum has been the industry's standard dummy text ever since the 1500s, when an unknown printer took a galley of type and scrambled it to make a type specimen Lorem Ipsum is simply dummy text of the printing and typesetting industry. Lorem Ipsum has been the industry's standard dummy text ever since the 1500s,</p>
  <div class="abs ribbon"><span>SPECIAL OFFER</span></div>
</article>

<section class="abs why-best"></section>
<div class="abs tabs">
  <div class="tab active">Why Best ?</div>
  <div class="tab">Features</div>
  <div class="tab">Store the Goods</div>
</div>
<p class="abs tab-text">Lorem Ipsum is simply dummy text of the printing and typesetting industry. Lorem Ipsum has been the industry's standard dummy text ever since the 1500s. Lorem Ipsum is simply dummy text of the printing and typesetting industry. Lorem Ipsum has been the industry's standard dummy text ever since the 1500s. Lorem Ipsum is simply dummy text of the printing and typesetting industry. Lorem Ipsum has been the industry's standard dummy text ever since the 1500s. Lorem Ipsum is simply dummy text of the printing and typesetting industry. Lorem Ipsum has been the industry's standard dummy text ever since the 1500s.</p>
<div class="abs devices" role="img" aria-label="Darstellung der Website auf Desktop, Laptop, Tablet und Smartphone"></div>

<div class="abs footer-line"></div>
<footer class="abs site-footer"></footer>
<h5 class="abs footer-h" style="left:112px">MENU</h5>
<h5 class="abs footer-h" style="left:478px">CONTACT&nbsp; US</h5>
<h5 class="abs footer-h" style="left:830px">GET &amp; TOUCH WITH US</h5>
<ul class="abs footer-links" style="left:112px;top:2987px">
  <li>HOME</li><li>SERVICES</li><li class="strong">ONLINE SHOP</li><li>BLOG</li><li>LEGAL</li><li>CONTACT</li>
</ul>
<ul class="abs footer-links" style="left:251px;top:2987px">
  <li>TERMS &amp; CONDITION</li><li>PRIVACY POLICY</li><li>SITEMAP</li>
</ul>
<div class="abs footer-brand"><span class="brand-mark"></span><span class="brand-name" style="font-size:12px">Feinreise Kellwinden</span></div>
<div class="abs contact-row" style="top:2987px"><svg width="18" height="24" viewBox="0 0 18 24"><path d="M9 23S2 14 2 9a7 7 0 0 1 14 0c0 5-7 14-7 14Z" fill="#fff"/><circle cx="9" cy="9" r="2.6" fill="#000"/></svg><span>Lorem Ipsum is simply dummy text of the<br>printing and typesetting industry</span></div>
<div class="abs contact-row" style="top:3059px"><svg width="20" height="14" viewBox="0 0 20 14" fill="none" stroke="#fff" stroke-width="1.4"><rect x="1" y="1" width="18" height="12"/><path d="m1 1 9 7 9-7"/></svg><span style="margin-top:-6px">info@feinreise-kellwinden.de</span></div>
<div class="abs contact-row" style="top:3105px"><svg width="24" height="24" viewBox="0 0 24 24"><path d="M6 2 9 7 7 9c1 3 5 7 8 8l2-2 5 3-2 4C11 22 2 13 2 4Z" fill="#fff"/></svg><span style="font-size:13px">000-555-0142</span></div>
<div class="abs field" style="top:2988px;height:35px">Name</div>
<div class="abs field" style="top:3035px;height:35px">Email id</div>
<div class="abs field" style="top:3082px;height:84px">Comments</div>
<div class="abs submit">SUBMIT</div>
<div class="abs copyright">copyright@ www.feinreise-kellwinden.de</div>

</body>
</html>
```